My new Bible based podcast needs a Podcast Cover Design for Plexora directory

I need a Podcast Cover Design design for my podcast listing in Plexora. The podcast is called Morning Lantern Calling Home. I would like something cheerful, warm, and fresh because I take a non-traditional approach to explaining how the Bible is relevant to people today. My goal is to get back to the original spirituality of the Bible without all the centuries of added man-made doctrines. It would be great to show a sense of peace and hope, with new possibilities. This is not like a floating corporate logo. I need it to be square and full color/design all the way to the edges.

I have resubmitted this project because I did not understand how to ask for a podcast cover design. If you already submitted for me, I apologize for not knowing how the system works. I did not give the best picture of what I needed.

Target Market(s)

People who want a fresh look at the Bible

Industry/Entity Type

Religious

Logo Text

Morning Lantern Calling Home

Colors

Designer to choose colors to be used in the design.

Requirements
Must have
• It must be square. The design should fill the space. See screen shot below of podcast cover designs on the Christianity/Spirituality page of Plexora directory so you can see where the podcast cover design needs to fit in and stand out.
• The final design will need to be:
• 3,000 x 3,000 pixels (but readable at 150 x 150)
• 72 dpi
• .jpg or .png format
• rgb color space
Nice to have
• Perhaps an open book suggesting the Bible, but not necessary.
Should not have
• No microphones or airwaves.

```html
<!DOCTYPE html>
<html lang="en">
<head>
<meta charset="utf-8">
<title>Morning Lantern Calling Home – Podcast Cover</title>
<link rel="stylesheet" href="https://fonts.googleapis.com/css2?family=Montserrat:wght@800&display=swap">
<style>
  :root {
    --glow-orange: #ff7a00;
    --ember: #f0452b;
    --rose: #ec1a4a;
    --cream: #f0fbee;
    --podcast-red: #e8352e;
    --ray: rgba(255, 255, 255, 0.16);
  }
  html, body {
    margin: 0;
    padding: 0;
    width: 1200px;
    height: 1200px;
    overflow: hidden;
  }
  .cover {
    position: relative;
    width: 1200px;
    height: 1200px;
    overflow: hidden;
    background: radial-gradient(circle at 416px 256px, var(--glow-orange) 0%, var(--ember) 48%, var(--rose) 85%);
    font-family: "Montserrat", sans-serif;
    font-weight: 800;
    color: var(--cream);
  }
  .rays {
    position: absolute;
    inset: 0;
  }
  .rays polygon { fill: var(--ray); }
  .mark-dot {
    position: absolute;
    left: 446px;
    top: 400px;
    width: 290px;
    height: 290px;
    border-radius: 50%;
    background: var(--cream);
  }
  .title {
    position: absolute;
    left: 46px;
    margin: 0;
    line-height: 1;
    white-space: nowrap;
  }
  .title-small {
    top: 676px;
    font-size: 64px;
    letter-spacing: 2px;
  }
  .title-large {
    top: 770px;
    font-size: 232px;
    letter-spacing: -6px;
  }
  .title-sub {
    top: 1070px;
    font-size: 80px;
    letter-spacing: -1px;
  }
  .podcast-tag {
    position: absolute;
    left: 714px;
    top: 1084px;
    width: 414px;
    height: 60px;
    background: var(--cream);
    color: var(--podcast-red);
    display: flex;
    align-items: center;
    justify-content: space-between;
    padding: 0 14px;
    box-sizing: border-box;
    font-size: 36px;
  }
</style>
</head>
<body>
  <div class="cover">
    <svg class="rays" viewBox="0 0 1200 1200" width="1200" height="1200" aria-hidden="true">
      <polygon points="52,34 96,34 400,360"/>
      <polygon points="385,34 410,34 528,352"/>
      <polygon points="616,34 634,34 626,268"/>
      <polygon points="842,34 866,34 722,352"/>
      <polygon points="1152,36 1152,78 848,362"/>
      <polygon points="46,332 46,362 392,488"/>
      <polygon points="1152,354 1152,380 858,488"/>
      <polygon points="46,574 46,594 310,586"/>
      <polygon points="1152,576 1152,594 942,586"/>
      <polygon points="46,790 46,820 392,680"/>
      <polygon points="1152,790 1152,815 858,680"/>
      <polygon points="1152,1100 1152,1135 848,808"/>
    </svg>

    <div class="mark-dot" aria-hidden="true"></div>

    <h1 class="title-group">
      <span class="title title-small">MORNING</span>
      <span class="title title-large">Lantern</span>
      <span class="title title-sub">Calling Home</span>
    </h1>

    <div class="podcast-tag">
      <span>P</span><span>O</span><span>D</span><span>C</span><span>A</span><span>S</span><span>T</span>
    </div>
  </div>
</body>
</html>
```